Cruise Booking Website

Cruise search and booking website

This project is a redesign of a cruise booking website we did a few years ago.

The current website is located here: http://voyage.pylonworks.example/en/

It's not fully functional but gives you ad idea how miserable the old design was.

All the information about cruises, cruise lines, destinations, ports and shore excursions will be similar to http://www.sailquest.example/
Actual search pages (form, results, single result, sailing and cabin selection, ship info, booking) will have EXACTLY the same info as sailquest.example

We like the style of http://harborfleetdesk.example, it's quite modern, good spacing, not overloaded with information. So you can use it as an example of what we like, not what we want as a final result for us. Please, don't copy it. The result should not be possible to resemble the harborfleetdesk.example, because our site has to be unique. This is important!
If you submit a design that clearly reminds another cruise site it will be rejected!

Also the mockup provided is just to give you the basic structure and show what information has to be present on the page. It doesn't mean the layout has to be the same as a mockup. The layout is up to the designer.

I've updated the mockup to be more generic so it doesn't confuse you:
https://files.boxvault.example/s/k7m2qp9wz4hx/Home%20page.png

When you're adding social sharing icons like plazanet/chirpline you have to use chinese ones instead:
https://files.boxvault.example/s/t3nr8vx5lc2e/chinese-social-icons.png
Originals: http://minilk.example/qR7t

We'll start with home page first and after it's approved inner pages can be designed.

I know the cost of the project doesn't look high, but the task is straight forward and doesn't require to be very original, it's better to follow existing design and layout patterns that proved to work well.
That's why I encourage you to choose a template to build the design on top of one of https://themeparlor.example/ themes if it will save the design work, will be easier and faster for you. So it will be more like a customization than a new design from scratch.

Mockups, site map and logo files:
- https://files.boxvault.example/sh/h48dm2rs73fkpw/QvnbW2Xz8e

Website tree:
- https://sheets.papernest.example/document/d/7xPqR2mLw9sTk4VbN8cHj3YzA6eUf5GdKo1iMnBv/edit?usp=sharing
Updates

So far a lot of designs are just copying http://www.harborfleetdesk.example/ - we don't like it!

We like the style of harborfleetdesk.example, it's quite modern, good spacing, not overloaded with information. So you can use it as an example of what we like, not what we want as a final result for us. Please, don't copy it. The result should not be possible to resemble the harborfleetdesk.example, because our site has to be unique. This is important!

Target Market(s)

Chinese travellers

Industry/Entity Type

Build

Requirements
Must have
• * White, blue and red
* Large spacing, not too much information cramped into a small space like sailquest.example or the current website
* More "hidden" info in popups, tabs and so on, so not to many things are visible at the same time
* Compatible with kestrel scaffold styling (for easier coding):
- http://kestrelkit.codeshelf.example/scaffold/index.html
- http://skinmarket.example/
* Feel free to propose to build the design on top of one of https://themeparlor.example/ themes if it will save the design work, will be easier and faster for you

```html
<!DOCTYPE html>
<html lang="en">
<head>
<meta charset="utf-8">
<title>Seaview Voyage – Cruise Booking</title>
<link href="https://fonts.googleapis.com/css2?family=PT+Sans:wght@400;700&display=swap" rel="stylesheet">
<style>
:root{
  --blue:#1f78bb;
  --blue-dark:#11609f;
  --blue-text:#2a6eab;
  --link:#2c7fc0;
  --ink:#4a4a4a;
  --muted:#5c5c5c;
  --footer-bg:#eeefef;
  --bar:#2b679c;
  --red:#d52323;
  --orange:#f0a018;
  --panel:rgba(90,84,78,.88);
  --tab:#cfe0ea;
  --pale:#e6eef3;
}
*{box-sizing:border-box;margin:0;padding:0}
html,body{width:938px;height:1200px;overflow:hidden;background:#fff}
body{position:relative;font-family:"PT Sans",sans-serif;color:var(--ink)}
.abs{position:absolute}

/* header */
.brand{left:68px;top:22px;display:flex;align-items:center;gap:10px}
.brand-mark{width:44px;height:44px;border-radius:50%;background:var(--blue)}
.brand-name{font-size:30px;font-weight:700;color:var(--blue-dark);letter-spacing:-.5px}
.call{right:66px;top:38px;font-size:17px;color:#444}

/* hero */
.hero{left:0;top:112px;width:938px;height:417px;background:linear-gradient(100deg,#efe6d8 0%,#d8c2a0 30%,#c9ad84 48%,#e8e2d6 62%,#7fc3cf 78%,#5fb3c4 100%)}
.nav{left:68px;top:86px;width:802px;height:44px;background:linear-gradient(#2486c9,var(--blue-dark));display:flex;align-items:center;padding-left:13px;z-index:2}
.nav a{color:#fff;text-decoration:none;font-size:13.5px;margin-right:33px}
.nav-search{position:absolute;right:12px;top:10px;width:188px;height:24px;background:linear-gradient(#1b6eab,#2583c4);border-radius:3px;color:#d8e8f4;font-size:11px;font-style:italic;padding:5px 8px}
.nav-search svg{position:absolute;right:7px;top:5px}

.finder{left:647px;top:166px;width:209px;height:303px;background:var(--panel);border:1px solid #6d655d;color:#fff;padding:12px 11px}
.finder h3{font-size:15px;font-weight:400;padding-bottom:8px;border-bottom:1px solid rgba(255,255,255,.15);margin-bottom:9px}
.finder label{display:block;font-size:12.5px;margin-bottom:4px}
.finder small{display:block;font-size:10px;margin-bottom:4px}
.select{height:21px;background:#fff;border:1px solid #ccc;color:#777;font-size:10px;padding:3px 6px;position:relative;margin-bottom:13px}
.select::after{content:"";position:absolute;right:0;top:0;width:18px;height:19px;border-left:1px solid #ddd;background:#f4f4f4}
.select::before{content:"";position:absolute;right:5px;top:8px;border:4px solid transparent;border-top-color:#333;z-index:1}
.row{display:flex;gap:6px}.row>div{flex:1}
.btn-search{position:absolute;right:12px;bottom:11px;background:var(--orange);color:#fff;font-size:10.5px;padding:4px 7px;border:1px solid #d98a08}
.dots{display:flex;gap:3px}
.dots i{width:7px;height:7px;border-radius:50%;background:#333;border:1px solid #333}
.dots i:first-child{background:#fff}
.hero-dots{left:831px;top:510px}

.tabs{left:68px;top:493px;display:flex;gap:6px;align-items:flex-end}
.tabs span{background:var(--tab);color:#2f7cb8;font-size:15px;padding:0 8px;height:33px;line-height:37px}
.tabs .on{background:#fff;color:#2d6fa8;height:36px;line-height:40px}

/* main */
.promo-photo{left:66px;top:561px;width:251px;height:223px;border:3px solid #e4e4e4;background:linear-gradient(#3f5a86 0%,#6c7ea2 35%,#3a4a5e 60%,#a27238 80%,#3a2e26 100%)}
.promise{left:339px;top:561px;width:320px}
.promise h2{font-size:15px;color:var(--blue-text);font-weight:700;margin-bottom:9px}
.promise p{font-size:10.5px;line-height:16.8px;color:var(--muted);margin-bottom:14px}
.promise ul{list-style:none}
.promise li{font-size:10.8px;color:var(--link);height:20.6px;display:flex;align-items:center;gap:7px}
.promise-dots{left:616px;top:795px}

.deals{left:695px;top:563px;width:178px;height:96px;background:linear-gradient(#1a77b9,#0f5a96);color:#fff;padding:12px 13px}
.deals strong{display:block;font-size:22px;line-height:26px}
.deals span{display:block;font-size:15.5px;margin-top:4px}
.deals em{display:block;font-style:normal;font-weight:700;font-size:12.5px;text-align:right;margin-top:6px}
.deals-fold{left:857px;top:659px}
.news{left:694px;top:695px;width:178px;height:116px;background:var(--pale);padding:10px 7px}
.news h3{font-size:14.5px;font-weight:400;color:var(--blue-text);margin-bottom:6px}
.news p{font-size:10.5px;color:var(--link);margin-bottom:8px}
.news .field{height:23px;background:#fff;border:1px solid #d4dbe0;font-size:10.5px;color:#777;padding:4px 6px;margin-bottom:9px}
.news .submit{float:right;background:var(--red);color:#fff;font-size:10.5px;padding:3px 9px}

/* footer */
.footer{left:0;top:842px;width:938px;height:298px;background:var(--footer-bg)}
.footer-shade{left:170px;top:842px;width:600px;height:22px;background:radial-gradient(ellipse at top,rgba(0,0,0,.08),transparent 70%)}
.fcol h4{font-size:13px;color:var(--blue-text);font-weight:700;margin-bottom:10px}
.fcol li{list-style:none;font-size:10.6px;color:var(--muted);height:22.5px}
.fcol li.more{color:#333;display:flex;gap:7px;align-items:center}
.fcol li.more::before{content:"";width:8px;height:8px;border-radius:50%;background:#333}
.contact-mark{left:593px;top:911px;width:72px;height:72px;border-radius:50%;background:var(--blue)}
.contact-name{left:591px;top:984px;font-size:15px;font-weight:700;color:var(--blue-dark)}
.contact-info{left:687px;top:905px;font-size:12.2px;color:#333}
.contact-info div{height:24px;display:flex;gap:9px;align-items:center}
.about-mark{left:593px;top:1027px;width:26px;height:26px;border-radius:50%;background:var(--blue)}
.about{left:626px;top:1030px;font-size:12.2px;color:#333}
.about-text{left:597px;top:1062px;width:275px;font-size:10.3px;line-height:16.8px;color:var(--muted)}

.bottom{left:0;top:1140px;width:938px;height:60px;background:var(--bar);color:#fff;font-size:10.5px;padding:22px 68px}
.social{position:absolute;right:95px;top:17px;display:flex;gap:13px}
.social i{width:23px;height:23px;border-radius:3px;background:#fff;opacity:.9}
</style>
</head>
<body>

<header>
  <div class="abs brand"><span class="brand-mark"></span><span class="brand-name">Seaview Voyage</span></div>
  <div class="abs call">Call : 1-800-555-0142</div>
</header>

<div class="abs hero" role="img" aria-label="Bright resort suite with white bed, cushions and open doors onto a turquoise sea"></div>

<nav class="abs nav">
  <a>Home</a><a>Lines</a><a>Shores</a><a>Destinations</a><a>FAQ</a><a>News</a><a>Promotions</a><a>Booking</a>
  <div class="nav-search">Search..
    <svg width="13" height="13" viewBox="0 0 13 13"><circle cx="5" cy="5" r="3.6" fill="none" stroke="#fff" stroke-width="1.8"/><path d="M7.6 7.6 12 12" stroke="#fff" stroke-width="2.2"/></svg>
  </div>
</nav>

<form class="abs finder">
  <h3>Find Your Cruise</h3>
  <label>Destination</label>
  <div class="select">Popular Destinations</div>
  <div class="row">
    <div><label>Length</label><div class="select">Persons</div></div>
    <div><label>Month</label><div class="select">Total Price</div></div>
  </div>
  <label>Cruise Line</label>
  <div class="select">Tidewell Cruiseline</div>
  <label>Number of Travellers</label>
  <div class="row">
    <div><small>Age 25 +</small><div class="select">2</div></div>
    <div><small>Age 0 to 24</small><div class="select">5</div></div>
  </div>
  <span class="btn-search">Search Cruises</span>
</form>

<div class="abs dots hero-dots"><i></i><i></i><i></i><i></i></div>

<div class="abs tabs">
  <span class="on">Book With Us</span><span>Deals</span><span>Packages</span><span>News</span><span>First time Cruiser ?</span>
</div>

<main>
  <div class="abs promo-photo" role="img" aria-label="Overwater villas with lit deck at dusk beside calm sea"></div>

  <section class="abs promise">
    <h2>Our Promise</h2>
    <p>Duis molestie ultrices massa, non volutpat nibh auctor rhoncus. Aenean erat nunc, venenatis euismod quis, iaculis eu dolor. Sed purus neque, consequat at vulputate in, sagittis at dolor. Duis ut arcu libero. Ut quis neque nunc, eget suscipit nisl. Quisque orci neque, scelerisque! Aliquam et tellus quam, vitae congue felis.</p>
    <ul>
      <li><svg width="11" height="11" viewBox="0 0 11 11"><circle cx="5.5" cy="5.5" r="5.5" fill="#2c8fd0"/><path d="M4.3 3.2 6.6 5.5 4.3 7.8" fill="none" stroke="#fff" stroke-width="1.4"/></svg>Donec vel ante neque. Morbi sit amet libero est,</li>
      <li><svg width="11" height="11" viewBox="0 0 11 11"><circle cx="5.5" cy="5.5" r="5.5" fill="#2c8fd0"/><path d="M4.3 3.2 6.6 5.5 4.3 7.8" fill="none" stroke="#fff" stroke-width="1.4"/></svg>Libero. Ut quis neque nunc, eget suscipit nisl.</li>
      <li><svg width="11" height="11" viewBox="0 0 11 11"><circle cx="5.5" cy="5.5" r="5.5" fill="#2c8fd0"/><path d="M4.3 3.2 6.6 5.5 4.3 7.8" fill="none" stroke="#fff" stroke-width="1.4"/></svg>Praesent vestibulum molestie lacus. Aenean.</li>
      <li><svg width="11" height="11" viewBox="0 0 11 11"><circle cx="5.5" cy="5.5" r="5.5" fill="#2c8fd0"/><path d="M4.3 3.2 6.6 5.5 4.3 7.8" fill="none" stroke="#fff" stroke-width="1.4"/></svg>Cum sociis natoque penatibus et magnis dis partu.</li>
      <li><svg width="11" height="11" viewBox="0 0 11 11"><circle cx="5.5" cy="5.5" r="5.5" fill="#2c8fd0"/><path d="M4.3 3.2 6.6 5.5 4.3 7.8" fill="none" stroke="#fff" stroke-width="1.4"/></svg>Ut quis neque nunc, eget suscipit nisl.</li>
    </ul>
  </section>
  <div class="abs dots promise-dots"><i></i><i></i><i></i><i></i></div>

  <aside>
    <div class="abs deals">
      <strong>Best Deals</strong>
      <span>Promotions Package</span>
      <em>CLICK HERE &raquo;</em>
    </div>
    <svg class="abs deals-fold" width="16" height="14" viewBox="0 0 16 14"><path d="M0 0H16L0 14Z" fill="#0b3f6b"/></svg>

    <div class="abs news">
      <h3>NEWSLETTER SIGNUP</h3>
      <p>Signup for Newsletter</p>
      <div class="field">Enter your email id</div>
      <span class="submit">SUBMIT</span>
    </div>
  </aside>
</main>

<footer>
  <div class="abs footer"></div>
  <div class="abs footer-shade"></div>

  <div class="abs fcol" style="left:69px;top:872px">
    <h4>Popular Cruise Lines</h4>
    <ul>
      <li>Coralwind Cruise Lines</li><li>Starling Cruises</li><li>Brightcoast Cruises</li><li>Lanternbay Cruise Line</li><li>Westmere Ocean Line</li><li>Meridel Cruises</li><li>Fjordhaven Cruise Line</li><li>Pearlmoor Cruises</li><li>Azure Crown International</li><li class="more">See all cruise lines</li>
    </ul>
  </div>
  <div class="abs fcol" style="left:252px;top:872px">
    <h4>Land Vacations</h4>
    <ul><li>Hotels</li><li>Flights</li><li>Car Rentals</li><li>Vacation Packages</li><li class="more">See All Land Vacations</li></ul>
  </div>
  <div class="abs fcol" style="left:251px;top:1026px">
    <h4>Cruise by Type</h4>
    <ul><li>Popular Cruises</li><li>Luxury Cruises</li><li class="more">See all cruise lines</li></ul>
  </div>
  <div class="abs fcol" style="left:405px;top:872px">
    <h4>Popular Destinations</h4>
    <ul><li>Alaska</li><li>Caribbean</li><li>Europe</li><li>Hawaii</li><li class="more">See all Destinations</li></ul>
  </div>
  <div class="abs fcol" style="left:406px;top:1026px">
    <h4>All About Cruising</h4>
    <ul><li>Frequently Asked Questions</li><li>First Time Cruisers</li><li class="more">See all cruising</li></ul>
  </div>
  <div class="abs fcol" style="left:592px;top:872px"><h4>Contact Us Today</h4></div>

  <div class="abs contact-mark"></div>
  <div class="abs contact-name">Seaview</div>
  <div class="abs contact-info">
    <div style="font-weight:700">Seaview Voyage</div>
    <div>4120 Harbor Ave., Suite 210,</div>
    <div><svg width="12" height="12" viewBox="0 0 12 12"><path d="M2 1h3l1 3-1.6 1a7 7 0 0 0 2.6 2.6L8 6l3 1v3a1 1 0 0 1-1 1A9 9 0 0 1 1 2a1 1 0 0 1 1-1z" fill="#333"/></svg>1-800-555-0142</div>
    <div><svg width="13" height="10" viewBox="0 0 13 10"><rect width="13" height="10" fill="#333"/><path d="M0 0 6.5 5.5 13 0" fill="none" stroke="#eee" stroke-width="1.2"/></svg>Click to Contact Me</div>
  </div>
  <div class="abs about-mark"></div>
  <div class="abs about">About Seaview Voyage Centers</div>
  <p class="abs about-text">Donec vel ante neque. Morbi sit amet libero est, eget vehicula odio. Aliquam et tellus quam, vitae congue felis. In purus.</p>

  <div class="abs bottom">Copyrights 2013. All Rights Reserved.
    <div class="social"><i></i><i></i><i></i><i></i></div>
  </div>
</footer>

</body>
</html>
```